Web design for financial services

A modern web design of financial services (brokerage firm)
Req.s and technology tags :
- Very mobile friendly.
- One paged with some inner pages.
- Animated sticky header .
- Member login area for e-trade.
- Support RTL language.
- HTML & CSS.

The logo will be Home link
• MPTR :
WHO WE ARE
Content :
i) Board of Directors
ii) Mission Statement
iii) Corporate Values
iv) Regulations
• Financial Services :
WHAT WE DO
Content:
i) Electronic trading
ii) Trading desk
iii) Institutional
iv) Investors Education
• News
• Market Tools
• Forms---- opens new page
• Careers---- opens new page
• Contact Us----opens new page

The website is :
http://www.mptr-doha-example.com/

The logo need some changes to be more modern and impressively , but with keeping same structure .

Some related websites :
https://www.lv-bourse.example/

financial market

Financial Service

Coded - Design and coding required

2 page

• same fonts of http://www.kwdholdings.example/

• - Very mobile friendly.
• - One paged with some inner pages.
• - Animated sticky header .
• - Member login area for e-trade.
• - Support RTL language.
• - HTML & CSS.
• Slider , some Qatari theme,
• i like the video inside the home page
• ex :http://www.kwdholdings.example/

```html
<!DOCTYPE html>
<html lang="en">
<head>
<meta charset="utf-8">
<title>MPTR – Brokers at Doha Bourse</title>
<link rel="stylesheet" href="https://fonts.googleapis.com/css2?family=Open+Sans:wght@400;600;700&display=swap">
<style>
:root{
  --red:#b83b34;
  --red-band:#c0413a;
  --ink:#2d2d2d;
  --text:#555;
  --muted:#888;
  --light:#f1f1f1;
  --header:#ececec;
  --line:#cfcfcf;
  --footer:#2a2a2a;
  --white:#fff;
  --sun:#f4b45a;
  --sand:#d9b48a;
  --gulf:#2f8a8c;
  --dusk:#3a3d45;
}
*{box-sizing:border-box;margin:0;padding:0}
html,body{width:1200px;height:2687px;overflow:hidden}
body{font-family:"Open Sans",Arial,sans-serif;color:var(--text);background:var(--white);position:relative}
a{color:inherit;text-decoration:none}
h1,h2,h3{font-weight:400}

/* header */
.site-header{position:absolute;top:0;left:0;width:1200px;height:120px;background:var(--header)}
.brand{position:absolute;left:131px;top:34px;display:flex;align-items:center;gap:10px}
.brand-mark{width:14px;height:14px;background:var(--red)}
.brand-name{font-weight:700;font-size:30px;color:var(--red);letter-spacing:1px}
.header-tools{position:absolute;right:133px;top:23px;display:flex;gap:14px}
.tool-btn{height:34px;border:1px solid var(--line);background:var(--white);font-size:10px;color:var(--muted);display:flex;align-items:center;gap:6px;padding:0 14px;border-radius:2px}
.tool-btn svg{display:block}
.main-nav{position:absolute;right:133px;top:82px;display:flex;gap:29px;font-size:11px;font-weight:600;color:var(--ink);text-transform:uppercase}
.main-nav .active{color:var(--red)}

/* hero */
.hero{position:absolute;top:120px;left:0;width:1200px;height:493px;
  background:
    radial-gradient(ellipse 420px 200px at 90px 360px,rgba(255,190,90,.95) 0%,rgba(240,150,70,.55) 40%,rgba(240,150,70,0) 100%),
    linear-gradient(90deg,rgba(0,0,0,0) 0%,rgba(0,0,0,0) 30%,rgba(35,40,52,.55) 45%,rgba(60,66,78,.35) 60%,rgba(30,34,44,.6) 78%,rgba(70,78,92,.3) 100%),
    linear-gradient(180deg,#7f8795 0%,#a6a39f 30%,#cfa378 55%,#8b6a52 72%,#3b3c42 88%,#2a2b30 100%)}
.hero-copy{position:absolute;top:168px;width:100%;text-align:center;color:var(--white)}
.hero-title{font-size:32px;font-weight:600;text-shadow:0 1px 4px rgba(0,0,0,.45)}
.hero-sub{font-size:20px;font-weight:600;margin-top:2px;text-shadow:0 1px 4px rgba(0,0,0,.45)}
.play-btn{position:absolute;left:573px;top:258px;width:54px;height:54px}

/* split rows */
.split{position:absolute;left:0;width:1200px;display:flex}
.split .panel{width:600px;height:100%;background:var(--light);position:relative}
.split .photo{width:600px;height:100%}
.who{top:613px;height:367px}
.what{top:980px;height:363px}
.section-title{font-size:32px;font-weight:700;color:var(--red);text-transform:uppercase;line-height:1}
.panel p{font-size:13px;line-height:24px;color:var(--text);text-align:justify}
.panel p a{color:var(--red)}
.who .panel .inner{position:absolute;left:131px;top:68px;width:442px}
.who .panel p{margin-top:16px}
.btn-row{display:flex;gap:9px;margin-top:20px}
.ghost-btn{height:45px;border:1px solid var(--line);background:var(--white);font-size:13px;color:var(--text);display:flex;align-items:center;justify-content:center;gap:8px;width:216px}
.what .panel .inner{position:absolute;left:27px;top:100px;width:440px}
.what .panel p{margin-top:16px}
.photo-city{background:
    radial-gradient(ellipse 260px 340px at 60px 330px,rgba(34,120,125,.95) 0%,rgba(34,120,125,.6) 45%,rgba(34,120,125,0) 100%),
    radial-gradient(ellipse 380px 200px at 420px 240px,rgba(120,135,150,.75) 0%,rgba(120,135,150,0) 100%),
    linear-gradient(180deg,#d6aa7a 0%,#cfae8a 22%,#a9a6a0 45%,#6f8a92 70%,#2f7f84 100%)}
.photo-meeting{background:
    radial-gradient(ellipse 200px 160px at 330px 170px,rgba(235,232,226,.9) 0%,rgba(235,232,226,0) 100%),
    radial-gradient(ellipse 180px 220px at 90px 120px,rgba(70,58,48,.85) 0%,rgba(70,58,48,0) 100%),
    linear-gradient(135deg,#4e4338 0%,#7c7064 35%,#a8a299 55%,#3c3f47 85%,#2e3037 100%)}

/* carousels */
.block{position:absolute;left:131px;width:936px}
.block-head{display:flex;justify-content:space-between;align-items:center}
.arrows{display:flex;gap:5px}
.arrow-box{width:24px;height:22px;border:1px solid var(--line);display:flex;align-items:center;justify-content:center;background:var(--white)}
.cards{display:flex;gap:19px;margin-top:18px}
.card{width:299px}
.card-img{height:160px}
.card-date{font-size:11px;color:var(--red);margin-top:14px}
.card-title{font-size:13px;font-weight:400;color:var(--ink);line-height:19px;margin-top:14px;padding-right:80px}
.card-text{font-size:10px;color:var(--muted);line-height:17px;margin-top:6px}
.card-more{font-size:10px;color:var(--ink);font-weight:600;margin-top:1px;display:block}
.news{top:1418px}
.tools{top:2035px}
.tools .card-name{font-size:19px;font-weight:400;color:var(--ink);margin-top:8px}
.tools .card-text{margin-top:2px}
.img-chart{background:radial-gradient(ellipse 120px 60px at 90px 70px,#aeb8d6 0%,rgba(174,184,214,0) 100%),linear-gradient(135deg,#f3f5f9,#dde3ee 55%,#eef0f4)}
.img-graph{background:radial-gradient(ellipse 70px 100px at 220px 90px,#d9b8a2 0%,rgba(217,184,162,0) 100%),linear-gradient(135deg,#85878c,#a4a6aa 55%,#b9bbbe)}
.img-tablet{background:radial-gradient(ellipse 110px 80px at 200px 90px,#e6e8ec 0%,rgba(230,232,236,0) 100%),linear-gradient(135deg,#2e2b29,#5b4a3e 45%,#8c8e92)}
.img-team{background:radial-gradient(ellipse 90px 80px at 230px 110px,#caa889 0%,rgba(202,168,137,0) 100%),linear-gradient(135deg,#6e5b4c,#9b8b7a 45%,#3f4450)}
.img-office{background:radial-gradient(ellipse 120px 140px at 90px 120px,#2a2c33 0%,rgba(42,44,51,0) 100%),linear-gradient(135deg,#c9663a,#d98a60 35%,#ece8e2 60%,#b7bcc5)}
.img-laptop{background:radial-gradient(ellipse 110px 70px at 180px 70px,#3c424c 0%,rgba(60,66,76,0) 100%),linear-gradient(135deg,#c2ccd7,#e6eaee 45%,#9aa3ad)}

/* partners */
.partners{position:absolute;top:1841px;left:0;width:1200px;height:120px;background:var(--light)}
.partners .nav-arrow{position:absolute;top:47px}
.partner-list{position:absolute;left:134px;width:932px;top:0;height:120px;display:flex;justify-content:space-between;align-items:center}
.partner{font-size:18px;font-weight:600;color:#5a5a5a;letter-spacing:1px}

/* e-trade */
.etrade{position:absolute;top:2457px;left:0;width:1200px;height:133px;background:var(--red-band)}
.etrade-title{position:absolute;left:256px;top:43px;font-size:32px;font-weight:700;color:var(--white)}
.field{position:absolute;top:48px;height:36px;background:var(--white);font-size:11px;color:var(--ink);display:flex;align-items:center;padding-left:10px}
.field-user{left:405px;width:215px}
.field-pass{left:636px;width:216px}
.etrade-btn{position:absolute;left:869px;top:48px;width:71px;height:36px;background:var(--footer);color:var(--white);font-size:11px;display:flex;align-items:center;justify-content:center}

/* footer */
.site-footer{position:absolute;top:2590px;left:0;width:1200px;height:97px;background:var(--footer);color:#aaa;font-size:10px}
.footer-links{position:absolute;left:133px;top:28px;display:flex;gap:10px}
.copyright{position:absolute;left:133px;top:54px}
.social{position:absolute;right:133px;top:28px;display:flex;gap:8px}
.social span{width:28px;height:28px;border-radius:50%;background:#d9d9d9}
</style>
</head>
<body>

<header class="site-header">
  <a class="brand" href="#"><span class="brand-mark"></span><span class="brand-name">MPTR</span></a>
  <div class="header-tools">
    <a class="tool-btn" href="#">
      <svg width="8" height="10" viewBox="0 0 8 10"><rect x="0.5" y="4" width="7" height="5.5" fill="#999"/><path d="M2 4V2.5a2 2 0 0 1 4 0V4" fill="none" stroke="#999"/></svg>Login</a>
    <a class="tool-btn" href="#">
      <svg width="14" height="9" viewBox="0 0 14 9"><rect width="14" height="9" fill="#3c4f8a"/><path d="M0 4.5h14M7 0v9" stroke="#c94040" stroke-width="2"/></svg>English
      <svg width="8" height="5" viewBox="0 0 8 5" style="margin-left:10px"><path d="M1 1l3 3 3-3" fill="none" stroke="#999"/></svg></a>
  </div>
  <nav class="main-nav">
    <a class="active" href="#">MPTR</a>
    <a href="#">Financial Services</a>
    <a href="#">News</a>
    <a href="#">Market Tool</a>
    <a href="#">Forms</a>
    <a href="#">Careers</a>
  </nav>
</header>

<section class="hero" role="img" aria-label="Doha skyline with glass towers and cranes at sunset">
  <div class="hero-copy">
    <h1 class="hero-title">Meridian Pearl Trading Co</h1>
    <p class="hero-sub">Brokers at Doha Bourse</p>
  </div>
  <svg class="play-btn" viewBox="0 0 54 54" aria-label="Play video">
    <circle cx="27" cy="27" r="25" fill="#fff"/>
    <circle cx="27" cy="27" r="19" fill="none" stroke="#b83b34" stroke-width="4"/>
    <path d="M22 17l14 10-14 10z" fill="#b83b34"/>
  </svg>
</section>

<section class="split who">
  <div class="panel">
    <div class="inner">
      <h2 class="section-title">Who We Are</h2>
      <p>Meridian Pearl Trading is a private Qatari company that aims to provide secure and technologically advanced methods of trading to its clients. Those facilities enables clients to trade faster, more secure &amp; private. Having this strategy in our in minds, with this online portal we begin. <a href="#">About MPTR</a></p>
      <div class="btn-row">
        <a class="ghost-btn" href="#"><svg width="11" height="11" viewBox="0 0 11 11"><circle cx="5.5" cy="5.5" r="5" fill="#555"/><path d="M0.5 5.5h10M5.5 0.5c-2 3-2 7 0 10M5.5 0.5c2 3 2 7 0 10" stroke="#fff" stroke-width=".8" fill="none"/></svg>Open New Account Online</a>
        <a class="ghost-btn" href="#"><svg width="10" height="12" viewBox="0 0 10 12"><path d="M1 .5h5.5L9 3v8.5H1z" fill="none" stroke="#555"/><path d="M3 6h4M3 8h4" stroke="#555"/></svg>Open New Account PDF</a>
      </div>
    </div>
  </div>
  <div class="photo photo-city" role="img" aria-label="Aerial view of the Doha West Bay towers beside the turquoise Gulf"></div>
</section>

<section class="split what">
  <div class="photo photo-meeting" role="img" aria-label="Team meeting around a wooden table with charts and laptops"></div>
  <div class="panel">
    <div class="inner">
      <h2 class="section-title">What We Do</h2>
      <p>Nullam vehicula justo in molestie laoreet. Vestibulum ac nibh dignissim, facilisis erat nec, rhoncus justo. Integer dolor nunc, ornare sit amet eros quis, pretium ullamcorper ligula. Curabitur lacinia nec ipsum vel semper. Vivamus justo erat, porttitor id efficitur ut, volutpat id odio. Pellentesque at elementum leo. <a href="#">Read more</a></p>
    </div>
  </div>
</section>

<section class="block news">
  <div class="block-head">
    <h2 class="section-title">Latest News</h2>
    <div class="arrows">
      <span class="arrow-box"><svg width="6" height="9" viewBox="0 0 6 9"><path d="M5 1L1.5 4.5 5 8" fill="none" stroke="#777"/></svg></span>
      <span class="arrow-box"><svg width="6" height="9" viewBox="0 0 6 9"><path d="M1 1l3.5 3.5L1 8" fill="none" stroke="#777"/></svg></span>
    </div>
  </div>
  <div class="cards">
    <article class="card">
      <div class="card-img img-chart" role="img" aria-label="Tablet showing bar charts on a desk"></div>
      <p class="card-date">1 February, 2017</p>
      <h3 class="card-title">Morbi nulla libero, tincidunt at condi mentum rhoncus.</h3>
      <p class="card-text">Pellentesque habitant morbi tristique senec-<br>tus et netus et malesuada fames.</p>
      <a class="card-more" href="#">More</a>
    </article>
    <article class="card">
      <div class="card-img img-graph" role="img" aria-label="Hand pointing at a rising line graph"></div>
      <p class="card-date">1 February, 2017</p>
      <h3 class="card-title">Morbi nulla libero, tincidunt at condi mentum rhoncus.</h3>
      <p class="card-text">Pellentesque habitant morbi tristique senec-<br>tus et netus et malesuada fames.</p>
      <a class="card-more" href="#">More</a>
    </article>
    <article class="card">
      <div class="card-img img-tablet" role="img" aria-label="Hands holding a tablet with market charts"></div>
      <p class="card-date">1 February, 2017</p>
      <h3 class="card-title">Morbi nulla libero, tincidunt at condi mentum rhoncus.</h3>
      <p class="card-text">Pellentesque habitant morbi tristique senec-<br>tus et netus et malesuada fames.</p>
      <a class="card-more" href="#">More</a>
    </article>
  </div>
</section>

<section class="partners">
  <svg class="nav-arrow" style="left:24px" width="14" height="26" viewBox="0 0 14 26"><path d="M12 2L2 13l10 11" fill="none" stroke="#999" stroke-width="2"/></svg>
  <div class="partner-list">
    <span class="partner">Ravel</span>
    <span class="partner">Halden</span>
    <span class="partner">Perrin</span>
    <span class="partner">Ostera</span>
    <span class="partner">Kenlow</span>
    <span class="partner">Zuma</span>
    <span class="partner">Ranvo</span>
  </div>
  <svg class="nav-arrow" style="right:24px" width="14" height="26" viewBox="0 0 14 26"><path d="M2 2l10 11L2 24" fill="none" stroke="#999" stroke-width="2"/></svg>
</section>

<section class="block tools">
  <div class="block-head">
    <h2 class="section-title">Market Tools</h2>
    <div class="arrows">
      <span class="arrow-box"><svg width="6" height="9" viewBox="0 0 6 9"><path d="M5 1L1.5 4.5 5 8" fill="none" stroke="#777"/></svg></span>
      <span class="arrow-box"><svg width="6" height="9" viewBox="0 0 6 9"><path d="M1 1l3.5 3.5L1 8" fill="none" stroke="#777"/></svg></span>
    </div>
  </div>
  <div class="cards">
    <article class="card">
      <div class="card-img img-team" role="img" aria-label="Colleagues talking in a modern office"></div>
      <h3 class="card-name">Most Active Company</h3>
      <p class="card-text">Pellentesque habitant morbi tristique senec-<br>tus et netus et malesuada fames.</p>
      <a class="card-more" href="#">More</a>
    </article>
    <article class="card">
      <div class="card-img img-office" role="img" aria-label="Business team standing in a brick-walled office"></div>
      <h3 class="card-name">Top Gainer</h3>
      <p class="card-text">Pellentesque habitant morbi tristique senec-<br>tus et netus et malesuada fames.</p>
      <a class="card-more" href="#">More</a>
    </article>
    <article class="card">
      <div class="card-img img-laptop" role="img" aria-label="Hands typing on a laptop showing stock charts"></div>
      <h3 class="card-name">Top Loser</h3>
      <p class="card-text">Pellentesque habitant morbi tristique senec-<br>tus et netus et malesuada fames.</p>
      <a class="card-more" href="#">More</a>
    </article>
  </div>
</section>

<section class="etrade">
  <h2 class="etrade-title">E-TRADE</h2>
  <div class="field field-user">Username</div>
  <div class="field field-pass">Password</div>
  <a class="etrade-btn" href="#">LOGIN</a>
</section>

<footer class="site-footer">
  <nav class="footer-links">
    <a href="#">Home</a><span>|</span><a href="#">About Us</a><span>|</span><a href="#">Services</a><span>|</span><a href="#">Knowledge Base</a><span>|</span><a href="#">E-Trade</a><span>|</span><a href="#">Contact Us</a>
  </nav>
  <p class="copyright">Copyright © 2017 Company name. All rights reserved.</p>
  <div class="social"><span></span><span></span><span></span></div>
</footer>

</body>
</html>
```